Detail Shop Business card design

i need a business card design for my new detailing company called 'Brisk's Polish Works'. i want an all black and white design . simple, direct and to the point. i want the designer to choose a fitting font to match the logothe front should have logo, address, phone and email and the back side should have a slogan and text indicating that we offer services on anything including cars, trucks, motorcycles and RVs. slogan will read "We put shine on your wheels"
maybe also very small on the back side the IG icon with Brisks_Polish_Works

phone 208.417.6352
address 3847 E Larkin Ave
Spokane WA 99214
email: BrisksPolish@mailvexo.com

Target Market(s)

all ages , auto enthusiasts

Industry/Entity Type

Automotive

Contact Information for Business Card

the front should have logo, address, phone and email and the back side should have a slogan and text indicating that we offer services on anything including cars, trucks, motorcycles and RVs. slogan will read "We put shine on your wheels"

phone 208.417.6352
address 3847 E Larkin Ave
Spokane WA 99214

Colors
000000
ffffff

Requirements
Must have
• bold font and very simple design with good spacing
Nice to have
• anything creative from the designer indicating we service any types of vehicles
Should not have
• any colors ,

```html
<!DOCTYPE html>
<html lang="en">
<head>
<meta charset="utf-8">
<title>Brisk's Polish Works – Business Card</title>
<link rel="stylesheet" href="https://fonts.googleapis.com/css2?family=Teko:wght@400;500&family=Roboto:wght@400;500&family=Roboto+Condensed:wght@400&family=Oswald:wght@500&family=Arimo:wght@700&display=swap">
<style>
  :root {
    --backdrop: #1e1e1e;
    --card: #f4f4f4;
    --ink: #111111;
    --ink-soft: #4a4a4a;
  }
  * { margin: 0; padding: 0; box-sizing: border-box; }
  html, body { width: 1200px; height: 960px; overflow: hidden; }
  body { background: var(--backdrop); position: relative; }

  .card {
    position: absolute;
    width: 600px;
    height: 343px;
    background: var(--card);
    color: var(--ink);
    text-align: center;
  }
  .card--front { left: 314px; top: 113px; }
  .card--back  { left: 311px; top: 472px; }

  .person-name {
    position: absolute; left: 0; right: 0; top: 122px;
    font-family: "Teko", sans-serif; font-weight: 500;
    font-size: 58px; line-height: 1; letter-spacing: 0.3px;
  }
  .person-role {
    position: absolute; left: 0; right: 0; top: 177px;
    font-family: "Roboto", sans-serif; font-weight: 500;
    font-size: 14px; color: var(--ink-soft); letter-spacing: 0.3px;
  }
  .divider {
    position: absolute; left: 243px; top: 248px;
    width: 115px; height: 3px; background: var(--ink);
  }
  .contact {
    position: absolute; left: 0; right: 0; top: 265px;
    font-family: "Roboto Condensed", sans-serif;
    font-size: 13.5px; line-height: 20px; color: var(--ink-soft);
  }
  .contact span + span { margin-left: 5px; }

  .brand {
    position: absolute; left: 0; right: 0; top: 110px;
    display: flex; align-items: center; justify-content: center; gap: 14px;
  }
  .brand-dot { width: 22px; height: 22px; border-radius: 50%; background: var(--ink); }
  .brand-name {
    font-family: "Oswald", sans-serif; font-weight: 500;
    font-size: 38px; line-height: 1; text-transform: uppercase; letter-spacing: 1px;
  }
  .slogan {
    position: absolute; left: 0; right: 0; top: 272px;
    font-family: "Arimo", sans-serif; font-weight: 700;
    font-size: 16px; letter-spacing: 0.3px;
  }
  .slogan-rule {
    position: absolute; left: 137px; top: 293px;
    width: 325px; height: 2px; background: var(--ink);
  }
  .services {
    position: absolute; left: 0; right: 0; top: 297px;
    font-family: "Oswald", sans-serif; font-weight: 500;
    font-size: 14px; transform: scaleX(0.9);
  }
</style>
</head>
<body>
  <section class="card card--front">
    <h1 class="person-name">DALE PORTER</h1>
    <p class="person-role">CEO/FOUNDER</p>
    <div class="divider"></div>
    <p class="contact">
      3847 E Larkin Ave, Spokane WA 99214<br>
      <span>P: 208.417.6352</span><span>M: 836 271 5048</span><span>BrisksPolish@mailvexo.com</span><span>www.briskspolishworks.com</span>
    </p>
  </section>

  <section class="card card--back">
    <div class="brand">
      <span class="brand-dot"></span>
      <span class="brand-name">Brisk's Polish Works</span>
    </div>
    <p class="slogan">WE PUT SHINE ON YOUR WHEELS</p>
    <div class="slogan-rule"></div>
    <p class="services">we detail every kind of vehicle from cars and trucks to bikes &amp; RVs</p>
  </section>
</body>
</html>
```